TK Stationery - Modern Contemporary

Develop modern template for Letterhead and Stationery (business card, letterhead, envelopes) using the TK Logo and Icon

Colors
0054AA
0677BA
7BADD7
CADEEF
E8F1F8
00AB8E
00BBA5
67D7C9
C6EFE9
E9F9F6
EE7325
F08F49
F5BC92
FAE3D3
FDF4ED
6B429C
8869AF
B7A5CE
E3DAEB
F3F0F8

```html
<!DOCTYPE html>
<html lang="en">
<head>
<meta charset="utf-8">
<title>Tessa Kano Letterhead</title>
<link rel="stylesheet" href="https://fonts.googleapis.com/css2?family=Arimo:wght@400;700&family=Mulish:wght@700&display=swap">
<style>
  :root {
    --backdrop: #cdcccd;
    --paper: #ffffff;
    --navy: #262b47;
    --green: #3db275;
    --body-text: #555555;
    --heading-text: #505050;
    --signature-tone: #e9e9ec;
  }
  * { margin: 0; padding: 0; box-sizing: border-box; }
  html, body { width: 1173px; height: 1200px; overflow: hidden; }
  body { background: var(--backdrop); position: relative; font-family: "Arimo", Arial, sans-serif; }

  .letterhead {
    position: absolute; left: 230px; top: 96px;
    width: 713px; height: 1009px;
    background: var(--paper);
    overflow: hidden;
  }
  .brand-name {
    position: absolute; left: 64px; top: 54px;
    font-family: "Arimo", Arial, sans-serif;
    font-weight: 400; font-size: 36px; letter-spacing: 0.5px;
    color: var(--navy); line-height: 1;
  }
  .salutation {
    position: absolute; left: 66px; top: 310px;
    font-family: "Mulish", "Century Gothic", sans-serif;
    font-weight: 700; font-size: 16px; color: var(--heading-text);
  }
  .letter-body {
    position: absolute; left: 64px; top: 356px; width: 584px;
    font-size: 11.6px; line-height: 14.8px; color: var(--body-text);
    text-align: justify;
  }
  .letter-body p { margin-bottom: 12.5px; }
  .letter-body p:last-child { text-align: left; }
  .closing {
    position: absolute; left: 65px; top: 660px;
    font-family: "Mulish", "Century Gothic", sans-serif;
    font-weight: 700; font-size: 9px; color: var(--heading-text);
  }
  .signature {
    position: absolute; left: 64px; top: 702px;
    width: 118px; height: 34px;
    background: var(--signature-tone); border-radius: 3px;
  }
  .contact-list {
    position: absolute; left: 64px; top: 939px;
    list-style: none; font-size: 11.8px; line-height: 14.8px; color: var(--navy);
  }
  .contact-list li { display: flex; align-items: center; gap: 6px; }
  .contact-list svg { width: 10px; height: 10px; flex: none; }
  .contact-divider {
    position: absolute; left: 218px; top: 937px;
    width: 1.5px; height: 31px; background: var(--navy);
  }
  .address {
    position: absolute; left: 234px; top: 939px;
    font-size: 11.8px; line-height: 14.8px; color: var(--navy);
  }
  .footer-bands {
    position: absolute; left: 0; top: 978px; width: 713px; height: 31px;
  }
  .web-address {
    position: absolute; left: 493px; top: 980px;
    font-weight: 700; font-size: 14px; line-height: 20px; color: var(--paper);
  }
</style>
</head>
<body>
  <main class="letterhead">
    <div class="brand-name">tessa kano</div>

    <h1 class="salutation">Dear Mr. Smith,</h1>

    <section class="letter-body">
      <p>Lorem ipsum dolor sit amet, consectetuer adipiscing elit, sed diam nonmmy nibh euismod tincidunt ut laoreet dolore magna aliquam erat volutpat. Ut wisi enim ad minim veniam, quis nostrud exerci tationmcorper suscipit lobortis nisl ut aliquip ex ea commodo consequat. Duis autem vel eum iriure dolor in hendrerit in vulputate velit esse molestie consequat, vel illum dolore eu feugiat</p>
      <p>Rorem ipsum dolor sit amet, consectetuer adipiscing elit, sed diam nonmmy nibh euismod tincidunt ut laoreet dolore magna aliquam erat volutpat. Ut wisi enim ad minim veniam, quis nostrud exerci tationmcorper suscipit lobortis nisl ut aliquip ex ea commodo consequat. Duis autem vel eum iriure dolor in hendrerit in vulputate velit esse molest</p>
      <p>Dorem ipsum dolor sit amet, consectetuer adipiscing elit, sed diam nonmmy nibh euismod tincidunt ut laoreet dolore magna aliquam erat volutpat. Ut wisi enim ad minim veniam, quis nostrud exerci tationmcorper suscipit lobortis nisl ut aliquip ex ea commodo consequat. Duis autem vel eum iriure dolor in hendrerit in suscipit lobortis nisl ut aliquip ex ea commodo consequat. Duis autem vel eum iriure dolor in hendrerit in vulputate velit esse molestie consequat, vel illum</p>
      <p>Sorem ipsum dolor sit amet, consectetuer adipiscing elit, sed diam nonmmy nibh euismod tincidunt ut laoreet dolore magna aliquam erat volutpat. Ut wisi enim ad minim veniam, quis nostrud exerci tationmcorper suscipit lobortis nisl ut aliquip ex ea commodo consequat. Duis autem vel eum iriure dolor in</p>
    </section>

    <p class="closing">Sincerely,</p>
    <div class="signature" role="img" aria-label="Handwritten signature"></div>

    <ul class="contact-list">
      <li>
        <svg viewBox="0 0 10 10" aria-hidden="true"><path d="M2 0.8 L3.6 2.8 L2.8 3.8 C3.4 5.2 4.6 6.5 6.1 7.2 L7.1 6.3 L9.2 7.9 L8.2 9.4 C4.4 9.2 0.8 5.6 0.6 1.8 Z" fill="var(--green)"/></svg>
        <span>123-456-2100</span>
      </li>
      <li>
        <svg viewBox="0 0 10 10" aria-hidden="true"><rect x="0.5" y="2" width="9" height="6.5" fill="var(--green)"/><path d="M0.8 2.4 L5 5.8 L9.2 2.4" stroke="#fff" stroke-width="0.9" fill="none"/></svg>
        <span>info@tessakano.com</span>
      </li>
    </ul>
    <div class="contact-divider"></div>
    <address class="address" style="font-style:normal">Your address, city<br>state, ZIP 0000</address>

    <svg class="footer-bands" viewBox="0 0 713 31" aria-hidden="true">
      <polygon points="0,6 452,6 446,11 0,11" fill="var(--navy)"/>
      <path d="M0,21 H428 C445,21 452,15 462,7 C470,1 476,0 486,0 H713 V31 H0 Z" fill="var(--green)"/>
    </svg>
    <div class="web-address">www.tessakano.com</div>
  </main>
</body>
</html>
```